Design a New Business Card for Our Company

We are looking for fresh, unique, and a modern business card that reflects our roots as digital marketing agency focused on SEM.

Industry/Entity Type

Marketing

Contact Information for Business Card

looking for very unique out of the box designs. clean and modern that compliments our logo

Requirements
Must have
• colors should match our logo
• Front should have name, address, email, and phone/fax of the person, phone/fax are the same number
• back should have our url

```html
<!DOCTYPE html>
<html lang="en">
<head>
<meta charset="utf-8">
<title>Veltrix Media – Business Card</title>
<link href="https://fonts.googleapis.com/css2?family=Roboto:wght@300;400;500&display=swap" rel="stylesheet">
<style>
  :root {
    --stage: #b3b1b1;
    --brand-blue: #5b97d0;
    --paper: #ffffff;
    --ink-light: #ffffff;
    --card-shadow: rgba(0, 0, 0, 0.35);
  }
  * { box-sizing: border-box; margin: 0; padding: 0; }
  html, body { width: 1200px; height: 1000px; overflow: hidden; }
  body {
    position: relative;
    background: var(--stage);
    font-family: "Roboto", Arial, sans-serif;
    color: var(--ink-light);
  }
  .card {
    position: absolute;
    background: var(--brand-blue);
    box-shadow: 8px 10px 14px var(--card-shadow);
    overflow: hidden;
  }

  /* Back side: URL */
  .card-back { left: 322px; top: 34px; width: 557px; height: 339px; }
  .card-back .pattern-field {
    position: absolute; left: 0; width: 100%;
    background: var(--brand-blue);
  }
  .card-back .pattern-top { top: 0; height: 124px; }
  .card-back .pattern-bottom { top: 215px; height: 124px; }
  .card-back .logo-band {
    position: absolute; left: 0; top: 124px; width: 100%; height: 91px;
    background: var(--paper);
    display: flex; align-items: center; justify-content: center;
  }
  .card-back .url {
    position: absolute; left: 0; right: 0; top: 300px;
    text-align: center; font-size: 17px; font-weight: 500;
  }

  /* Brand name set as text */
  .brand {
    display: flex; align-items: center; gap: 12px;
    color: var(--brand-blue);
    font-weight: 500; font-size: 40px; letter-spacing: 0.5px;
  }
  .brand-dot {
    width: 34px; height: 34px; border-radius: 50%;
    background: var(--brand-blue);
  }

  /* Front side: contact */
  .card-front { left: 434px; top: 410px; width: 340px; height: 556px; }
  .card-front .logo-panel {
    position: absolute; left: 0; top: 0; width: 100%; height: 162px;
    background: var(--paper);
    display: flex; align-items: center; justify-content: center;
  }
  .card-front .logo-panel .brand { font-size: 36px; }
  .card-front .logo-panel .brand-dot { width: 30px; height: 30px; }
  .contact {
    position: absolute; left: 0; top: 162px; width: 100%; height: 394px;
    text-align: center;
  }
  .person { position: absolute; top: 28px; left: 0; width: 100%; }
  .person-name {
    font-size: 19px; font-weight: 500; line-height: 26px;
    display: flex; align-items: center; justify-content: center; gap: 4px;
  }
  .person-name::before, .person-name::after {
    content: ""; height: 2px; width: 114px; background: var(--ink-light);
  }
  .person-role { font-size: 14px; font-weight: 400; line-height: 18px; }
  .detail {
    position: absolute; left: 0; width: 100%;
    font-size: 14.5px; font-weight: 300; line-height: 18.5px;
  }
  .detail svg { display: block; margin: 0 auto 4px; width: 26px; height: 26px; }
  .detail-address { top: 88px; }
  .detail-phone { top: 184px; }
  .detail-fax { top: 240px; }
  .detail-email { top: 309px; }
</style>
</head>
<body>

<section class="card card-back" aria-label="Card back">
  <div class="pattern-field pattern-top" role="img" aria-label="Faint repeating brand pattern on blue"></div>
  <div class="logo-band">
    <div class="brand"><span class="brand-dot"></span><span class="brand-name">Veltrix Media</span></div>
  </div>
  <div class="pattern-field pattern-bottom" role="img" aria-label="Faint repeating brand pattern on blue"></div>
  <p class="url">www.veltrixmedia.com</p>
</section>

<section class="card card-front" aria-label="Card front">
  <div class="logo-panel">
    <div class="brand"><span class="brand-dot"></span><span class="brand-name">Veltrix Media</span></div>
  </div>
  <div class="contact" role="img" aria-label="Blue field with faint scattered circle decoration">
    <div class="person">
      <p class="person-name">Sam Carter</p>
      <p class="person-role">President</p>
    </div>

    <div class="detail detail-address">
      <svg viewBox="0 0 26 26" fill="none" stroke="#fff" stroke-width="1.6">
        <circle cx="13" cy="13" r="11.5"/>
        <path d="M13 20c-3-3.6-4.6-6-4.6-8a4.6 4.6 0 0 1 9.2 0c0 2-1.6 4.4-4.6 8z"/>
        <circle cx="13" cy="11.8" r="1.6"/>
      </svg>
      <p>4870 Maple Ridge Rd<br>Glen Harbor,<br>CA 90210 USA</p>
    </div>

    <div class="detail detail-phone">
      <svg viewBox="0 0 26 26" fill="none" stroke="#fff" stroke-width="1.6">
        <circle cx="13" cy="13" r="11.5"/>
        <path d="M9 7.5l2.2 2.8-1.3 1.5c.9 1.8 2.3 3.2 4.1 4.1l1.5-1.3 2.8 2.2-1.4 2c-4.6-.6-8.5-4.5-9.1-9.1z" fill="#fff"/>
      </svg>
      <p>555-014-2290</p>
    </div>

    <div class="detail detail-fax">
      <svg viewBox="0 0 26 26" fill="none" stroke="#fff" stroke-width="1.6">
        <circle cx="13" cy="13" r="11.5"/>
        <rect x="9.5" y="6.5" width="7" height="4"/>
        <rect x="7" y="10.5" width="12" height="6" fill="#fff"/>
        <rect x="9.5" y="14.5" width="7" height="5" fill="#5b97d0"/>
      </svg>
      <p>555-014-2290</p>
    </div>

    <div class="detail detail-email">
      <svg viewBox="0 0 26 26" fill="none" stroke="#fff" stroke-width="1.6">
        <circle cx="13" cy="13" r="11.5"/>
        <rect x="7" y="8.5" width="12" height="9" fill="#fff"/>
        <path d="M7 8.5l6 5 6-5" stroke="#5b97d0"/>
      </svg>
      <p>hello@veltrix.com</p>
    </div>
  </div>
</section>

</body>
</html>
```